Top Pour Web site design

The aim of Top Pour is to provide an online service which allows customers to pre-order drinks and gain incentives such as fast entry, special offers (drinks, entry fees), as well as allowing customers to compare drinking establishments based upon costs and ratings.

what is required is the design of the pages stated below completed to the specifications.

Target Market(s)

The target market of Top Pour is men and women between the ages of 18 to 26 mainly. Within the age range of 18 to 26 the more specific target groups

Industry/Entity Type

Online

Requirements
Must have
• What is required to be designed

Website to be viewable on different systems e.g desktop, laptop and for mobile devices a mobile friendly page

Home page

Logo
Company name
Log in
Sign up
Help
Social media links, Follow us link

Bar, pub, club search function
Search by postcode, establishment type, distance

Pictorial instructions of how to use the site like ( quick dine). The stages are 1) select location 2) build order and pay 3) pick up from bar

Pre load results of establishments

Drinking establishment sign up

Map showing search results

List of results

My basket window which shows your order

Pop out box for customer sign up

Buttons for FAQ, general information, company information, Privacy policy ect at bottom of page

The home page is required to be Clear, simple, easy to use and stylish but not over the top with to much information which will confuse the customers. The preloaded results need to be obvious and where can be seen. The pictorial instructions should go below the preloaded results. Once the search criteria has been filled in and has been submitted the preloaded results and pictorial instructions will be removed and be replaced by the map and search results.

Drinking establishment personal page requires

Details of drinking establishment (name, address, contact, map)
list of drinks avliable
My basket
Special Offers
Gallery
Calendar
Reviews section at the bottom

When a person clicks on a drinking establishment page what that person should see when they open the page is company name logo
with a list of the drinks they offer and special offers. Tabs or buttons for gallery, establishment details, calender and special offers should be located along top or down the left. when they are clicked on they will replace the menu.

The colour scheme is based around the logo which is attached. We do not want any pink or overly bright colours which would not go with the logo.

A site which we like is this one
http://www.quick-dine.example.co.uk/
this site is perfect simple, clear but also good looking. If you need inspiration you should use this site as a starting point.
Should not have
• what should be avoided is a site which like this one http://platepoint.example.co.uk/~beta/?gclid=XQMWpLaRtnfGDsHYbTqeKZPLv

it is to complicated with bad font and colours. The site just feels cheesy and not classy. we like very little about this site

```html
<!DOCTYPE html>
<html lang="en">
<head>
<meta charset="utf-8">
<title>Top Pour – Drinking Establishment</title>
<link rel="stylesheet" href="https://fonts.googleapis.com/css2?family=Open+Sans:wght@400;600;700&family=Delius&display=swap">
<style>
:root{
  --brand:#2e3192;
  --brand-dark:#2b2d8c;
  --btn-top:#7373e6;
  --btn-bottom:#3a3cc4;
  --text:#333;
  --muted:#555;
  --line:#d8d8d8;
  --dash:#b9b9b9;
  --gold:#d9a514;
  --side-top:#f1f1f1;
  --side-bottom:#d8d8d8;
  --page:#fff;
}
*{box-sizing:border-box;margin:0;padding:0}
html,body{width:1187px;height:1200px;overflow:hidden;background:var(--page)}
body{font-family:"Open Sans",Arial,sans-serif;color:var(--text);position:relative}
.top-edge{position:absolute;left:0;top:0;width:1187px;height:6px;background:#c9c9c9}
.abs{position:absolute}

/* header */
.brand{left:182px;top:20px;display:flex;align-items:center;gap:14px}
.brand-mark{width:72px;height:72px;border-radius:50%;border:7px solid #8a8a8a}
.brand-name{font-size:31px;font-weight:600;color:var(--brand)}
.cart{left:551px;top:61px;font-size:13px;color:var(--muted);display:flex;align-items:center;gap:5px}
.cart b{color:#2244dd}
.btn-check{margin-left:5px;border:1px solid #bbb;background:linear-gradient(#f3f3f3,#d9d9d9);padding:2px 10px;font-size:13px;color:#444}
.social{display:flex;gap:5px}
.social span{width:24px;height:24px;border-radius:50%;background:var(--brand);display:block}
.social.top{left:903px;top:24px}
.account{left:816px;top:60px;font-size:15px;font-weight:600;color:#444}
.help{left:927px;top:58px;width:81px;height:26px;border:1px solid #bbb;border-radius:4px;font-size:12px;color:var(--brand);text-align:center;line-height:24px;box-shadow:0 2px 2px rgba(0,0,0,.12)}
.rule{left:181px;top:123px;width:820px;height:1px;background:var(--line)}
.page-title{left:182px;top:131px;font-family:"Delius",cursive;font-size:25px;font-weight:400;color:var(--brand)}

/* sidebar */
.map{left:181px;top:184px;width:197px;height:161px;border:1px solid #ccc;padding:5px;background:#fff}
.map div{width:100%;height:100%;background:linear-gradient(135deg,#e9e4d6,#d6e7c8 60%,#cfd8e6)}
.side-nav{left:181px;top:355px;width:197px;list-style:none}
.side-nav li{height:32px;margin-bottom:7px;border:1px solid #c4c4c4;background:linear-gradient(var(--side-top),var(--side-bottom));display:flex;align-items:center;gap:9px;padding-left:10px;font-size:14px;color:#444}
.side-nav svg{width:16px;height:16px;fill:#8d8d8d}

/* venue */
.venue-photo{left:396px;top:184px;width:109px;height:109px;background:linear-gradient(#5a5a5a,#2b2b2b 60%,#777);box-shadow:0 1px 3px rgba(0,0,0,.4)}
.venue-name{left:521px;top:178px;font-size:17px;font-weight:700;color:var(--brand);line-height:24px}
.facts{left:521px;top:203px;font-size:12.5px;line-height:20.3px;display:grid;grid-template-columns:91px auto;white-space:nowrap}
.facts dt{font-weight:600}
.facts dd{margin:0}
.facts dd::before{content:": "}
.cost{color:var(--gold);font-weight:700;letter-spacing:2px}
.mugs{display:inline-flex;gap:4px;vertical-align:-1px}
.mugs svg{width:13px;height:12px}
.day-select{left:864px;top:210px;width:136px;height:32px;border:1px solid #bbb;font-size:12.5px;color:#444;display:flex;align-items:center;justify-content:space-between;padding:0 7px}
.btn-order-now{left:865px;top:251px;width:135px;height:32px;font-size:16px}
.btn{background:linear-gradient(var(--btn-top),var(--btn-bottom));color:#fff;font-weight:700;text-align:center;border-radius:2px;box-shadow:0 2px 3px rgba(0,0,0,.3);display:flex;align-items:center;justify-content:center}

/* offers */
.offers{left:396px;top:312px;width:600px;border-top:1px dashed var(--dash)}
.offers h2{font-family:"Delius",cursive;font-weight:400;font-size:20px;color:#444;margin-top:15px;line-height:26px}
.category{margin-top:22px}
.category:first-of-type{margin-top:6px}
.category h3{font-size:16px;font-weight:600;color:var(--brand);line-height:20px;margin-bottom:11px}
.items{display:grid;grid-template-columns:293px 293px;column-gap:13px;row-gap:18px}
.item{position:relative;height:91px;border-bottom:1px dashed var(--dash)}
.item .photo{position:absolute;left:1px;top:0;width:72px;height:72px;border:1px solid #aaa}
.item h4{position:absolute;left:78px;top:-5px;font-size:14px;font-weight:600;color:#333;white-space:nowrap}
.item p{position:absolute;left:78px;top:16px;font-size:12.5px;color:#444;white-space:nowrap}
.item .qty{position:absolute;left:77px;top:42px;width:75px;height:31px;border:1px solid #ccc;font-size:12.5px;color:#555;display:flex;align-items:center;justify-content:center}
.item .btn{position:absolute;left:158px;top:42px;width:118px;height:31px;font-size:14px}

/* footer */
.footer{left:0;top:1098px;width:1187px;height:102px;background:var(--brand-dark)}
.footer-links{left:179px;top:1130px;font-size:13px;color:#fff}
.copyright{left:179px;top:1150px;font-size:12.5px;color:#b9bbe6}
.social.bottom{left:895px;top:1134px}
.social.bottom span{background:#fff}
</style>
</head>
<body>
<div class="top-edge"></div>

<header>
  <div class="abs brand"><span class="brand-mark"></span><span class="brand-name">Top Pour</span></div>
  <div class="abs cart">
    <svg width="14" height="12" viewBox="0 0 14 12"><path d="M0 1h3l2 7h7l2-6H4" fill="none" stroke="#555" stroke-width="1.6"/><circle cx="6" cy="10.5" r="1.3" fill="#555"/><circle cx="11" cy="10.5" r="1.3" fill="#555"/></svg>
    <span><b>0</b> items | Subtotal : <b>£0.0</b></span>
    <span class="btn-check">Checkout</span>
  </div>
  <div class="abs social top"><span></span><span></span><span></span><span></span></div>
  <div class="abs account">Log in . Sign up</div>
  <div class="abs help">NEED HELP</div>
</header>
<div class="abs rule"></div>
<h1 class="abs page-title">Drinking Establishment</h1>

<aside>
  <div class="abs map"><div role="img" aria-label="Street map showing the establishment location"></div></div>
  <ul class="abs side-nav">
    <li><svg viewBox="0 0 16 16"><path d="M1 9 9 1h6v6l-8 8z"/></svg>ENTRY TICKETS</li>
    <li><svg viewBox="0 0 16 16"><circle cx="8" cy="8" r="6"/></svg>SPECIAL OFFERS</li>
    <li><svg viewBox="0 0 16 16"><path d="M1 3h14v12H1zM3 6v7h10V6z"/></svg>CALENDER</li>
    <li><svg viewBox="0 0 16 16"><path d="M1 2h14v12H1zM3 12h10L9 7l-3 3-1-1z"/></svg>GALLERY</li>
    <li><svg viewBox="0 0 16 16"><path d="M1 3h14v10H1zM2 4l6 5 6-5"/></svg>CONTACT DETAILS</li>
  </ul>
</aside>

<section>
  <div class="abs venue-photo" role="img" aria-label="Photo of the pub frontage"></div>
  <h2 class="abs venue-name">The LANTERN</h2>
  <dl class="abs facts">
    <dt>Provides</dt><dd>Food &amp; Drink</dd>
    <dt>Special offers</dt><dd>15% Off</dd>
    <dt>Cost</dt><dd><span class="cost">£££££</span></dd>
    <dt>Rating</dt><dd><span class="mugs">
      <svg viewBox="0 0 13 12"><path d="M1 1h8v10H1zM9 3h3v5H9" fill="#4b4bd6"/></svg>
      <svg viewBox="0 0 13 12"><path d="M1 1h8v10H1zM9 3h3v5H9" fill="#4b4bd6"/></svg>
      <svg viewBox="0 0 13 12"><path d="M1 1h8v10H1zM9 3h3v5H9" fill="#4b4bd6"/></svg>
      <svg viewBox="0 0 13 12"><path d="M1 1h8v10H1zM9 3h3v5H9" fill="#4b4bd6"/></svg>
      <svg viewBox="0 0 13 12"><path d="M1 1h8v10H1zM9 3h3v5H9" fill="#c4c4c4"/></svg>
    </span></dd>
  </dl>
  <div class="abs day-select">Select Order Day <svg width="8" height="6" viewBox="0 0 8 6"><path d="M0 0h8L4 6z" fill="#333"/></svg></div>
  <div class="abs btn btn-order-now">ORDER NOW</div>
</section>

<main class="abs offers">
  <h2>Establishment also offers</h2>

  <div class="category">
    <h3>Wines</h3>
    <div class="items">
      <div class="item"><div class="photo" role="img" aria-label="Red wine splashing in a glass" style="background:linear-gradient(135deg,#fff,#9b1b2c)"></div><h4>Duis sed lectus sit amet</h4><p>Nulla cursus ligula nec neque porttitor</p><span class="qty">How Many</span><span class="btn">ADD TO ORDER</span></div>
      <div class="item"><div class="photo" role="img" aria-label="Glass of red wine with grapes" style="background:linear-gradient(#6e7a3a,#b01c2a 60%,#556)"></div><h4>Donec non urna et ligula</h4><p>Etiam tempor sapien ac arcu</p><span class="qty">How Many</span><span class="btn">ADD TO ORDER</span></div>
      <div class="item"><div class="photo" role="img" aria-label="Glass of red wine" style="background:linear-gradient(135deg,#e2b15a,#6d1410)"></div><h4>Nullam nisi risus</h4><p>Nullam enim magna, laoreet ut</p><span class="qty">How Many</span><span class="btn">ADD TO ORDER</span></div>
      <div class="item"><div class="photo" role="img" aria-label="Wine being poured from a bottle" style="background:linear-gradient(135deg,#fff,#c02236)"></div><h4>Maecenas non lorem</h4><p>Praesent et nulla nisl</p><span class="qty">How Many</span><span class="btn">ADD TO ORDER</span></div>
    </div>
  </div>

  <div class="category">
    <h3>Beers</h3>
    <div class="items">
      <div class="item"><div class="photo" role="img" aria-label="Beer splashing into a glass" style="background:radial-gradient(#e9c87a,#3a2410)"></div><h4>Duis sed lectus sit amet</h4><p>Nulla cursus ligula nec neque porttitor</p><span class="qty">How Many</span><span class="btn">ADD TO ORDER</span></div>
      <div class="item"><div class="photo" role="img" aria-label="Several glasses of beer" style="background:linear-gradient(#f1efe9,#d9982e 60%,#7a5a30)"></div><h4>Donec non urna et ligula</h4><p>Etiam tempor sapien ac arcu</p><span class="qty">How Many</span><span class="btn">ADD TO ORDER</span></div>
    </div>
  </div>

  <div class="category">
    <h3>Cocktails</h3>
    <div class="items">
      <div class="item"><div class="photo" role="img" aria-label="Red cocktails being served" style="background:linear-gradient(#c8201a,#ef5a25)"></div><h4>Duis sed lectus sit amet</h4><p>Nulla cursus ligula nec neque porttitor</p><span class="qty">How Many</span><span class="btn">ADD TO ORDER</span></div>
      <div class="item"><div class="photo" role="img" aria-label="Row of cocktail glasses outdoors" style="background:linear-gradient(#e9e4d8,#e2625a 50%,#6a7a4a)"></div><h4>Donec non urna et ligula</h4><p>Etiam tempor sapien ac arcu</p><span class="qty">How Many</span><span class="btn">ADD TO ORDER</span></div>
    </div>
  </div>

  <div class="category">
    <h3>Non alcoholic</h3>
    <div class="items">
      <div class="item"><div class="photo" role="img" aria-label="Orange fruit drink with straw" style="background:radial-gradient(#f06a2a 35%,#fff 70%)"></div><h4>Duis sed lectus sit amet</h4><p>Nulla cursus ligula nec neque porttitor</p><span class="qty">How Many</span><span class="btn">ADD TO ORDER</span></div>
      <div class="item"><div class="photo" role="img" aria-label="Strawberry smoothie with berries" style="background:linear-gradient(#c6e2a0,#f2c7c0 50%,#c4242a)"></div><h4>Donec non urna et ligula</h4><p>Etiam tempor sapien ac arcu</p><span class="qty">How Many</span><span class="btn">ADD TO ORDER</span></div>
    </div>
  </div>
</main>

<footer>
  <div class="abs footer"></div>
  <nav class="abs footer-links">FAQ &nbsp;|&nbsp; general information &nbsp;|&nbsp; company information &nbsp;|&nbsp; Privacy policy</nav>
  <div class="abs copyright">Copyright © 2013 Top Pour. All rights reserved</div>
  <div class="abs social bottom"><span></span><span></span><span></span><span></span></div>
</footer>
</body>
</html>
```